Need a flyer to leave behind when visiting clients or at shows

Glossy colorful tri-fold flyer with the same information that is on my web site www.corvelbmq.com. I am open to a little modern or creative take on the typical brochure. I created the web site so I can provide any raw files needed from it. I would also like the ability to edit this flyer in the future in Adobe Photoshop Elements

```html
<!DOCTYPE html>
<html lang="en">
<head>
<meta charset="utf-8">
<title>Lumivar Healthcare Solutions – Tri-fold Brochure</title>
<link rel="stylesheet" href="https://fonts.googleapis.com/css2?family=Montserrat:wght@400;500;600;700;800&family=Oswald:wght@300;400;600&display=swap">
<style>
  :root {
    --purple: #7b3fc4;
    --purple-deep: #5d2aa0;
    --black: #141214;
    --white: #ffffff;
    --paper: #f3f2f4;
    --ink: #1d1b1f;
    --stage: #dcdcdc;
  }
  * { box-sizing: border-box; margin: 0; padding: 0; }
  html, body {
    width: 837px; height: 1200px; overflow: hidden;
    background: var(--stage);
    font-family: "Montserrat", sans-serif;
  }
  .brochure {
    position: absolute; left: 30px; top: 300px;
    width: 777px; height: 600px;
    background: var(--paper);
    box-shadow: 0 18px 28px rgba(0,0,0,0.28);
    overflow: hidden;
  }
  .brochure__art { position: absolute; inset: 0; }
  .panel { position: absolute; top: 0; height: 600px; }
  .panel--about { left: 0; width: 253px; }
  .panel--contact { left: 253px; width: 257px; }
  .panel--cover { left: 510px; width: 267px; }

  .site-tag {
    position: absolute; bottom: 16px; left: 50%; transform: translateX(-50%);
    width: 154px; height: 17px;
    border: 1px solid var(--purple);
    background: rgba(255,255,255,0.85);
    font-size: 9.5px; letter-spacing: 2px; color: var(--ink);
    text-align: center; line-height: 15px; font-weight: 500;
    white-space: nowrap;
  }
  .panel--cover .site-tag { background: transparent; color: var(--white); border-color: var(--white); }

  /* About panel */
  .about__title {
    position: absolute; left: 10px; top: 292px;
    font-size: 19px; font-weight: 800; color: var(--ink);
  }
  .about__rule { position: absolute; left: 10px; top: 322px; width: 45px; height: 3px; background: var(--purple); }
  .about__item { position: absolute; left: 0; width: 245px; }
  .about__label {
    display: inline-block; background: var(--purple); color: var(--white);
    font-size: 10.5px; font-weight: 700; padding: 3px 12px 3px 10px;
    border-radius: 0 10px 10px 0;
  }
  .about__text { margin: 9px 0 0 10px; font-size: 7.6px; line-height: 1.45; color: var(--ink); }

  /* Contact panel */
  .brand-name { color: var(--white); font-weight: 700; line-height: 1; white-space: nowrap; }
  .contact__brand { position: absolute; left: 0; right: 0; top: 32px; text-align: center; }
  .contact__brand .brand-name { font-size: 40px; letter-spacing: -1px; }
  .contact__brand .brand-sub { font-size: 12px; letter-spacing: 0.6px; margin-top: 6px; }
  .contact__pill {
    position: absolute; left: 47px; top: 148px; width: 163px; height: 23px;
    background: var(--purple); border-radius: 12px;
    color: var(--white); font-size: 16px; font-weight: 800; text-align: center; line-height: 23px;
  }
  .contact__icons { position: absolute; top: 183px; left: 0; right: 0; display: flex; justify-content: center; gap: 14px; }
  .contact__phone {
    position: absolute; top: 214px; left: 0; right: 0; text-align: center;
    font-family: "Oswald", sans-serif; font-weight: 600; font-size: 33px; line-height: 1.2;
    color: var(--white); white-space: nowrap;
  }
  .contact__email {
    position: absolute; left: 19px; top: 273px; width: 218px; height: 22px;
    border: 1px solid var(--purple); color: var(--white);
    font-size: 11px; letter-spacing: 1.6px; text-align: center; line-height: 20px;
    white-space: nowrap;
  }

  /* Cover panel */
  .cover__brand { position: absolute; left: 14px; top: 30px; }
  .cover__brand .brand-name { font-size: 26px; letter-spacing: -0.5px; }
  .cover__brand .brand-sub { font-size: 7px; letter-spacing: 0.4px; margin-top: 3px; }
  .cover__headline { position: absolute; left: 14px; top: 90px; color: var(--white); line-height: 1.08; }
  .cover__headline .h-strong { display: block; font-size: 22px; font-weight: 600; }
  .cover__headline .h-light { display: block; font-family: "Oswald", sans-serif; font-weight: 300; font-size: 25px; line-height: 1.15; }
  .cover__headline .h-mid { display: block; font-size: 16px; font-weight: 500; }
  .cover__headline .h-bold { display: block; font-size: 23px; font-weight: 800; }
  .cover__rule { position: absolute; left: 14px; top: 212px; width: 40px; height: 2px; background: var(--white); }
</style>
</head>
<body>
  <main class="brochure">
    <svg class="brochure__art" width="777" height="600" viewBox="0 0 777 600">
      <defs>
        <linearGradient id="people" x1="0" y1="0" x2="1" y2="1">
          <stop offset="0" stop-color="#d9cfc4"/><stop offset=".5" stop-color="#b3a498"/><stop offset="1" stop-color="#857873"/>
        </linearGradient>
        <linearGradient id="steth" x1="0" y1="0" x2="1" y2="1">
          <stop offset="0" stop-color="#dde1e7"/><stop offset=".6" stop-color="#abb5c3"/><stop offset="1" stop-color="#7f899a"/>
        </linearGradient>
        <linearGradient id="keys" x1="0" y1="0" x2="1" y2="1">
          <stop offset="0" stop-color="#6a7384"/><stop offset=".5" stop-color="#485267"/><stop offset="1" stop-color="#95a1b6"/>
        </linearGradient>
        <linearGradient id="violet" x1="0" y1="0" x2="1" y2="1">
          <stop offset="0" stop-color="#8a4fd3"/><stop offset="1" stop-color="#5d2aa0"/>
        </linearGradient>
      </defs>

      <!-- About panel -->
      <rect x="0" y="0" width="253" height="340" fill="url(#people)" role="img" aria-label="Photo area: two colleagues talking in a bright office"/>
      <polygon points="60,0 253,0 253,95 0,240 0,170" fill="#7b3fc4" opacity=".72"/>
      <polygon points="0,175 253,330 253,400 0,290" fill="#5d2aa0" opacity=".85"/>
      <polygon points="0,274 73,236 253,334 253,600 0,600" fill="#f3f2f4"/>
      <line x1="135" y1="282" x2="235" y2="333" stroke="#7b3fc4" stroke-width="1"/>
      <line x1="150" y1="298" x2="240" y2="346" stroke="#7b3fc4" stroke-width="1"/>

      <!-- Contact panel -->
      <rect x="253" y="320" width="257" height="280" fill="url(#steth)" role="img" aria-label="Photo area: stethoscope resting on an ECG printout"/>
      <polygon points="253,0 510,0 510,330 390,405 253,330" fill="#141214"/>
      <polygon points="253,325 370,390 253,490" fill="#7b3fc4" opacity=".9"/>
      <line x1="340" y1="440" x2="420" y2="390" stroke="#ffffff" stroke-width="1" opacity=".8"/>

      <!-- Cover panel -->
      <rect x="510" y="250" width="267" height="350" fill="url(#keys)" role="img" aria-label="Photo area: close-up of a hand typing on a keyboard"/>
      <polygon points="510,0 777,0 777,150 510,310" fill="url(#violet)"/>
      <polygon points="510,310 777,150 777,330 640,255" fill="#141214" opacity=".92"/>
      <line x1="695" y1="250" x2="755" y2="290" stroke="#ffffff" stroke-width="1" opacity=".8"/>
      <line x1="705" y1="265" x2="760" y2="302" stroke="#ffffff" stroke-width="1" opacity=".8"/>
    </svg>

    <section class="panel panel--about">
      <h2 class="about__title">ABOUT US</h2>
      <div class="about__rule"></div>
      <div class="about__item" style="top:355px">
        <span class="about__label">OUR MISSION</span>
        <p class="about__text">Partner with clients to increase the value &amp; security of their technology tools.</p>
      </div>
      <div class="about__item" style="top:426px">
        <span class="about__label">OUR GOAL</span>
        <p class="about__text">Become the premiere consulting company for Information Technology in the post-acute care industries.</p>
      </div>
      <div class="about__item" style="top:497px">
        <span class="about__label">OUR LEADERS</span>
        <p class="about__text">Dana Marlow, MHA, MBA, CHCIO</p>
      </div>
      <div class="site-tag">www.corvelbmq.com</div>
    </section>

    <section class="panel panel--contact">
      <div class="contact__brand">
        <div class="brand-name">Lumivar</div>
        <div class="brand-name brand-sub">HEALTHCARE SOLUTIONS</div>
      </div>
      <div class="contact__pill">CONTACT US</div>
      <div class="contact__icons">
        <svg width="24" height="24" viewBox="0 0 24 24" aria-label="Phone">
          <circle cx="12" cy="12" r="12" fill="#fff"/>
          <rect x="8.5" y="5.5" width="7" height="13" rx="1.5" fill="none" stroke="#141214" stroke-width="1.6"/>
          <circle cx="12" cy="16" r="0.9" fill="#141214"/>
        </svg>
        <svg width="24" height="24" viewBox="0 0 24 24" aria-label="Email">
          <circle cx="12" cy="12" r="12" fill="#fff"/>
          <rect x="6" y="8" width="12" height="8" fill="none" stroke="#141214" stroke-width="1.5"/>
          <polyline points="6,8 12,13 18,8" fill="none" stroke="#141214" stroke-width="1.5"/>
        </svg>
      </div>
      <div class="contact__phone">555 - 014 - 2790</div>
      <div class="contact__email">dmarlow@corvelbmq.com</div>
      <div class="site-tag">www.corvelbmq.com</div>
    </section>

    <section class="panel panel--cover">
      <div class="cover__brand">
        <div class="brand-name">Lumivar</div>
        <div class="brand-name brand-sub">HEALTHCARE SOLUTIONS</div>
      </div>
      <h1 class="cover__headline">
        <span class="h-strong">INCREASING</span>
        <span class="h-light">THE VALUE &amp; SECURITY</span>
        <span class="h-mid">OF YOUR TECHNOLOGY</span>
        <span class="h-bold">RESOURCES</span>
      </h1>
      <div class="cover__rule"></div>
      <div class="site-tag">www.corvelbmq.com</div>
    </section>
  </main>
</body>
</html>
```